Bramblewood Card Company Business Cards

We are a trading card store with Glimmorax, sports and other TCG cards, we need a business card design that encompasses a clean cut, modern style with a retro flare. website is bramblewoodcardco.com for reference. Can utilize a comic book era feel or a more modern outdoor feel to utilize the "Pacific Northwest" elements of tress, mountains, etc.

Industry/Entity Type

Trading cards and collectibles

Contact Information for Business Card

business name, email address, phone number, name, owner job title

Font styles to use
Sans Serif

```html
<!DOCTYPE html>
<html lang="en">
<head>
<meta charset="utf-8">
<title>Bramblewood Card Company – Business Cards</title>
<link rel="stylesheet" href="https://fonts.googleapis.com/css2?family=Montserrat:wght@400;500;700&display=swap">
<style>
  :root {
    --sky: #10bfe0;
    --ink: #1d1d1f;
    --slate: #6e6e70;
    --paper: #ffffff;
    --backdrop: #e9ebee;
  }
  * { box-sizing: border-box; margin: 0; padding: 0; }
  html, body { width: 1200px; height: 689px; overflow: hidden; }
  body {
    background: var(--backdrop);
    font-family: "Montserrat", Arial, sans-serif;
    color: var(--ink);
    position: relative;
  }
  .card {
    position: absolute;
    top: 180px;
    width: 550px;
    height: 314px;
    border-radius: 26px;
    box-shadow: 0 10px 30px rgba(0,0,0,.12);
    overflow: hidden;
  }
  .card-front { left: 35px; background: var(--sky); display: flex; align-items: center; justify-content: center; }
  .card-back { left: 615px; background: var(--paper); }

  .brand { display: flex; align-items: center; gap: 12px; }
  .brand-dot { width: 22px; height: 22px; border-radius: 50%; flex: none; }
  .brand-name { font-weight: 700; text-transform: uppercase; letter-spacing: 1px; line-height: 1.15; }
  .card-front .brand-dot { background: var(--paper); }
  .card-front .brand-name { color: var(--paper); font-size: 30px; }

  .card-back .brand { position: absolute; left: 30px; top: 132px; width: 190px; }
  .card-back .brand-dot { background: var(--sky); width: 14px; height: 14px; }
  .card-back .brand-name { color: var(--slate); font-size: 16px; letter-spacing: .5px; }

  .divider { position: absolute; left: 232px; top: 64px; width: 2px; height: 188px; background: var(--sky); }

  .details { position: absolute; left: 254px; top: 60px; right: 30px; }
  .person-name { color: var(--sky); font-weight: 700; font-size: 25px; letter-spacing: .3px; line-height: 1; white-space: nowrap; }
  .person-role { font-size: 13px; margin-top: 7px; }
  .region { color: var(--sky); font-size: 13px; margin-top: 15px; }
  .address { font-size: 13px; margin-top: 3px; }
  .contact-list { list-style: none; margin-top: 15px; }
  .contact-list li { display: flex; align-items: center; gap: 8px; font-size: 13px; line-height: 1.7; white-space: nowrap; }
  .contact-list svg { width: 12px; height: 12px; flex: none; }
</style>
</head>
<body>
  <section class="card card-front" aria-label="Card front">
    <div class="brand">
      <span class="brand-dot"></span>
      <span class="brand-name">Bramblewood<br>Card Company</span>
    </div>
  </section>

  <section class="card card-back" aria-label="Card back">
    <div class="brand">
      <span class="brand-dot"></span>
      <span class="brand-name">Bramblewood<br>Card Company</span>
    </div>
    <div class="divider"></div>
    <div class="details">
      <h1 class="person-name">OWEN HARLOW</h1>
      <p class="person-role">Managing Director</p>
      <p class="region">Pacific Northwest</p>
      <p class="address">Your address, City</p>
      <ul class="contact-list">
        <li>
          <svg viewBox="0 0 12 12" aria-hidden="true"><path fill="#10bfe0" d="M2.5 1h2l1 2.5-1.3.9a6 6 0 0 0 3.4 3.4l.9-1.3 2.5 1v2c0 .6-.4 1-1 1A9.5 9.5 0 0 1 1.5 2c0-.6.4-1 1-1z"/></svg>
          123 456 789
        </li>
        <li>
          <svg viewBox="0 0 12 12" aria-hidden="true"><rect x="1" y="2.5" width="10" height="7" rx="1" fill="#10bfe0"/><path d="M1.5 3l4.5 3.5L10.5 3" fill="none" stroke="#fff" stroke-width="1"/></svg>
          info@bramblewoodcardco.com
        </li>
        <li>
          <svg viewBox="0 0 12 12" aria-hidden="true"><circle cx="6" cy="6" r="5" fill="#10bfe0"/><path d="M1 6h10M6 1c-2 2.6-2 7.4 0 10M6 1c2 2.6 2 7.4 0 10" fill="none" stroke="#fff" stroke-width=".8"/></svg>
          www.bramblewoodcardco.com
        </li>
      </ul>
    </div>
  </section>
</body>
</html>
```